Traineeship Flyer Design Project

Requirements:
• 1 x A4 page flyer (double sided)
1st page; target market 15-19 yr old, looking for young/fresh, exciting, eye catching
2nd page: same look/feel – target market – parents/person to determine if there is value to devoting energy to this qualification (potentially less busy in design)
• Use of high quality logos: 1. Valtrexo 2. Nationally recognised training logo
Ideally wanting to keep amount of copy to the page layout as attached, although designer is free to interpret the layout of copy on each page, although Valtrexo will accept alternative presentation if designer sees new way to combine information
• Valtrexo does not have a set colour palette so there are no restrictions/guidelines to follow
Updates
Hi, All files including brief and logos have now been updated.
Reason: Hi everyone
Please refer to design submission below for the only design that was deemed to cover off on the brief as the starting point - in regards to producing a design that appeals to target market of young person (15-19) in regards to self selecting to take up further study
Hi everyone
Can you please view the 3 remaining designs that are in contention (out of 30+ submitted) - Design 1528020 ; 1510098; 1510087; I will be providing additional feedback to these designers, as that come closer to the mark of appealing to younger "potential trainee" - the collateral needs to make the young student want to pick up the flyer (eye catching/interesting) and then be motivated to want to self elect - "beg parents" to take up the option. **PLEASE NOTE - I have uploaded a colour swatch now, and would appreciate if desgins could use these colours (not a requirement to use base colours of blue a silver as base if an exciting image needs to come from leaning on "secondary colours" (brighter) as being the predominant colours.
Many thanks, appreciate being able to see such an active community of designers involved in this website
Target Market(s)
1st page; target market 15-19 yr old, looking for young/fresh, exciting, eye catching. same look/feel – target market – parents/person to decide on
Industry/Entity Type
Training
Look and feel

```html
<!DOCTYPE html>
<html lang="en">
<head>
<meta charset="utf-8">
<title>Valtrexo National Traineeships Flyer</title>
<link href="https://fonts.googleapis.com/css2?family=Arimo:wght@400;700&family=Roboto+Condensed:wght@700&family=Tinos&family=Gelasio:ital,wght@1,500;1,700&display=swap" rel="stylesheet">
<style>
:root{
  --navy:#1d2a6e;
  --navy-deep:#141c52;
  --navy-light:#2c3f94;
  --sand:#cdc5b8;
  --sand-light:#ddd6cb;
  --text-grey:#4a4a4a;
  --ink-blue:#23256e;
  --white:#ffffff;
  --circle:#efefef;
  --step1:#7f8a2a;
  --step2:#9a7a2a;
  --step3:#a32a2e;
  --step4:#5b2e9a;
  --step5:#1f7f35;
  --step6:#1e6e93;
}
*{margin:0;padding:0;box-sizing:border-box}
html,body{width:1200px;height:800px;overflow:hidden;background:#e9e9e9}
.flyer{position:relative;width:1200px;height:800px;overflow:hidden;
  background:linear-gradient(180deg,var(--sand-light),var(--sand));}
.hero{position:absolute;left:0;top:0;width:1200px;height:470px;
  background:linear-gradient(135deg,var(--navy-deep) 0%,var(--navy-light) 45%,var(--navy) 100%);}
.brand{position:absolute;left:0;right:0;top:26px;display:flex;justify-content:center;align-items:center;gap:14px;
  color:var(--white);font-family:"Tinos",serif;font-size:50px;}
.brand-mark{width:38px;height:38px;background:var(--white)}
.headline{position:absolute;left:0;right:0;top:92px;text-align:center;color:var(--white);
  font-family:"Arimo",sans-serif;font-weight:700;font-size:66px;letter-spacing:1px}
.photo{position:absolute;left:48px;top:180px;width:540px;height:270px;border:8px solid var(--white);
  background:linear-gradient(120deg,#2d2f33 0%,#7a5a48 40%,#b8342f 60%,#8b8d8f 100%);
  box-shadow:0 6px 14px rgba(0,0,0,.4)}
.pitch{position:absolute;left:620px;top:180px;width:540px;text-align:center;color:var(--white);font-family:"Arimo",sans-serif}
.pitch-lead{font-size:40px;line-height:1.1;color:#e6e8f2}
.pitch-free{font-size:68px;font-weight:700;line-height:1.1}
.pitch-rule{height:1px;margin:10px 10px 12px;background:linear-gradient(90deg,transparent,#8d97c9,transparent)}
.pitch-tag{font-family:"Roboto Condensed",sans-serif;font-weight:700;font-size:44px;line-height:1.15;color:#e8e8ee}
.steps{position:absolute;left:0;top:478px;width:1200px;height:180px}
.step{position:absolute;top:0;width:200px;height:180px}
.step-circle{position:absolute;left:26px;top:0;width:148px;height:140px;border-radius:50%;background:var(--circle);
  border:1px solid #b8b2a8;display:flex;align-items:center;justify-content:center;text-align:center;
  font-family:"Tinos",serif;font-size:21px;line-height:1.05;color:#333}
.step-pill{position:absolute;left:15px;top:146px;width:170px;height:28px;border-radius:6px;color:var(--white);
  font-family:"Gelasio",serif;font-style:italic;font-weight:700;font-size:18px;text-align:center;line-height:28px}
.step-arrow{position:absolute;right:-8px;top:62px;width:14px;height:16px}
.body-copy{position:absolute;left:30px;top:670px;width:1150px;font-family:"Arimo",sans-serif;color:var(--text-grey)}
.qualification{font-size:32px}
.cost-question{margin-top:6px;display:inline-block;font-family:"Gelasio",serif;font-style:italic;font-weight:500;
  font-size:36px;color:var(--ink-blue);border-bottom:2px solid var(--ink-blue);padding-right:60px}
.cost-answer{margin-top:4px;font-size:27px}
</style>
</head>
<body>
<div class="flyer">
  <section class="hero">
    <div class="brand"><span class="brand-mark"></span><span>Valtrexo</span></div>
    <h1 class="headline">National Traineeships</h1>
    <div class="photo" role="img" aria-label="Photo of two electricians in hard hats testing a switchboard"></div>
    <div class="pitch">
      <p class="pitch-lead">Kick-Start Your<br>Career Today For</p>
      <p class="pitch-free">FREE!</p>
      <div class="pitch-rule"></div>
      <p class="pitch-tag">Get ahead of the game<br>Learn on the job</p>
    </div>
  </section>

  <section class="steps">
    <div class="step" style="left:0"><div class="step-circle">Information<br>session</div><div class="step-pill" style="background:var(--step1)">Step 01</div>
      <svg class="step-arrow" viewBox="0 0 14 16"><path d="M3 2l8 6-8 6" fill="none" stroke="#666" stroke-width="2"/></svg></div>
    <div class="step" style="left:200px"><div class="step-circle">Register<br>your<br>interest</div><div class="step-pill" style="background:var(--step2)">Step 02</div>
      <svg class="step-arrow" viewBox="0 0 14 16"><path d="M3 2l8 6-8 6" fill="none" stroke="#666" stroke-width="2"/></svg></div>
    <div class="step" style="left:400px"><div class="step-circle">Enrolment</div><div class="step-pill" style="background:var(--step3)">Step 03</div>
      <svg class="step-arrow" viewBox="0 0 14 16"><path d="M3 2l8 6-8 6" fill="none" stroke="#666" stroke-width="2"/></svg></div>
    <div class="step" style="left:600px"><div class="step-circle">Start<br>training</div><div class="step-pill" style="background:var(--step4)">Step 04</div>
      <svg class="step-arrow" viewBox="0 0 14 16"><path d="M3 2l8 6-8 6" fill="none" stroke="#666" stroke-width="2"/></svg></div>
    <div class="step" style="left:800px"><div class="step-circle">Practical<br>assessments</div><div class="step-pill" style="background:var(--step5)">Step 05</div>
      <svg class="step-arrow" viewBox="0 0 14 16"><path d="M3 2l8 6-8 6" fill="none" stroke="#666" stroke-width="2"/></svg></div>
    <div class="step" style="left:1000px"><div class="step-circle">Graduate</div><div class="step-pill" style="background:var(--step6)">Step 06</div></div>
  </section>

  <section class="body-copy">
    <p class="qualification">Gain a formal national qualification recognised by all employers Australia-wide</p>
    <h2 class="cost-question">How much will it cost?</h2>
    <p class="cost-answer">Nothing! The full course is provided by Valtrexo at no cost to you.</p>
  </section>
</div>
</body>
</html>
```